Frostvale Harborline LLC

we need a business card design

Industry/Entity Type

hvac

Contact Information for Business Card

my logo

Requirements
Must have
• my logo and same colors

```html
<!DOCTYPE html>
<html lang="en">
<head>
<meta charset="utf-8">
<title>Frostvale Harborline LLC — Business Card</title>
<link href="https://fonts.googleapis.com/css2?family=Montserrat:wght@400;500;700&display=swap" rel="stylesheet">
<style>
  :root {
    --brand-blue: #0b5ea8;
    --brand-blue-dark: #0a4f92;
    --accent-orange: #f5a623;
    --card-white: #ffffff;
    --ink: #1f1f1f;
    --stage: #e9ebee;
  }
  * { box-sizing: border-box; margin: 0; padding: 0; }
  html, body {
    width: 1200px; height: 874px; overflow: hidden;
    background: var(--stage);
    font-family: "Montserrat", Arial, sans-serif;
  }
  .canvas {
    position: relative; width: 1200px; height: 874px;
  }
  .card {
    position: absolute; left: 290px;
    width: 620px; height: 354px;
    border-radius: 22px;
    overflow: hidden;
    box-shadow: 0 6px 18px rgba(0,0,0,0.15);
  }
  .card--front { top: 64px; background: var(--brand-blue); }
  .card--back { top: 456px; background: var(--card-white); }

  .brand-mark {
    display: flex; align-items: center; gap: 14px;
    font-weight: 700; line-height: 1.1;
  }
  .brand-mark__dot {
    width: 22px; height: 22px; border-radius: 50%;
    background: var(--accent-orange); flex: none;
  }
  .card--front .brand-mark {
    position: absolute; inset: 0; justify-content: center;
    color: var(--card-white); font-size: 34px; text-align: center;
  }
  .card--back .brand-mark {
    position: absolute; right: 40px; top: 190px; width: 300px;
    color: var(--brand-blue); font-size: 25px;
  }

  .holder { position: absolute; left: 38px; top: 38px; }
  .holder__name { color: var(--brand-blue-dark); font-weight: 700; font-size: 25px; }
  .holder__title { color: var(--ink); font-size: 14px; margin-top: 2px; }

  .contact { position: absolute; left: 38px; top: 176px; color: var(--ink); font-size: 15px; }
  .contact__address { line-height: 1.3; margin-bottom: 14px; }
  .contact__row { display: flex; align-items: center; gap: 10px; line-height: 1.5; }
  .contact__icon { width: 14px; height: 14px; flex: none; }
</style>
</head>
<body>
<div class="canvas">
  <section class="card card--front">
    <div class="brand-mark"><span class="brand-mark__dot"></span>Frostvale Harborline LLC</div>
  </section>

  <section class="card card--back">
    <div class="holder">
      <p class="holder__name">Dana Whitcombe</p>
      <p class="holder__title">Managing Director</p>
    </div>

    <div class="contact">
      <p class="contact__address">48 Larkspur Avenue,<br>Brookhaven, NY 13402</p>
      <p class="contact__row">
        <svg class="contact__icon" viewBox="0 0 14 14"><rect x="3" y="0.8" width="8" height="12.4" rx="1.5" fill="none" stroke="#f5a623" stroke-width="1.4"/><circle cx="7" cy="10.8" r="0.9" fill="#f5a623"/></svg>
        +1 (315) 555-0182
      </p>
      <p class="contact__row">
        <svg class="contact__icon" viewBox="0 0 14 14"><rect x="0.5" y="2.5" width="13" height="9" rx="1" fill="#f5a623"/><path d="M1 3.2 7 8l6-4.8" fill="none" stroke="#fff" stroke-width="1.2"/></svg>
        info@frostvaleharbor.com
      </p>
      <p class="contact__row">
        <svg class="contact__icon" viewBox="0 0 14 14"><circle cx="7" cy="7" r="6" fill="none" stroke="#f5a623" stroke-width="1.4"/><ellipse cx="7" cy="7" rx="2.6" ry="6" fill="none" stroke="#f5a623" stroke-width="1.1"/><path d="M1 7h12" stroke="#f5a623" stroke-width="1.1"/></svg>
        www.frostvaleharbor.com
      </p>
    </div>

    <div class="brand-mark"><span class="brand-mark__dot"></span>Frostvale Harborline LLC</div>
  </section>
</div>
</body>
</html>
```